Simple Logo Design for Semi-Clear Plastic Frosted Card stock

Create a business card on frosted plastic. compliment existing logo elements with a tree trunk, roots, or seed at the lower half and the full logo both on the front.

Contact information will go on a solid portion of the back of this design since this card stock is semi-transparent.

It is important to consider this plastic card stock medium in your design. I found helpful tips and guides listed at vellaprint-sample.net: be careful to understand ink printed on plastic cards cannot have too much of a consistent print area or risks peeling and fine lines can easily scratch off.
Updates

2" x 3.5" 20PT Clear Plastic Business cards with Round corners Please get info or templates here: https://www.vellaprint-sample.net/product-detail/2-x-35-20pt-clear-plastic-business-cards-with-round-corners

Target Market(s)

Not for profit- religion

Industry/Entity Type

Business

Must include complementary elements to the existing logo

Font styles to use
Decorative

Colors
000000

Requirements
Must have
• Elements of community, nature and oneness. Such as: seed, roots, tree trunk, etc.
• Three lines of space on the back for Name, Title, Phone Number.
Nice to have
• I like a light use of decorative elements
Should not have
• No eyes, from faces or animals.

```html
<!DOCTYPE html>
<html lang="en">
<head>
<meta charset="utf-8">
<title>Steadfast Grove — Business Card</title>
<link rel="stylesheet" href="https://fonts.googleapis.com/css2?family=Questrial&family=Mulish:wght@400;700&display=swap">
<style>
  :root {
    --page-bg: #e6dfd4;
    --band-green: #4c9140;
    --band-green-dark: #3f7f36;
    --band-frost: #ecebe6;
    --band-teal: #2f6c64;
    --band-teal-dark: #285d56;
    --ink-teal: #1f5a55;
    --ink-dark: #3a4a48;
    --ink-name: #f1dcd9;
    --ink-light: #e2e6e3;
    --slash: #6aa14f;
  }
  * { margin: 0; padding: 0; box-sizing: border-box; }
  html, body {
    width: 1200px; height: 970px; overflow: hidden;
    background: var(--page-bg);
  }
  .card {
    position: absolute; left: 75px; top: 185px;
    width: 1050px; height: 600px;
    border-radius: 28px; overflow: hidden;
    box-shadow: 0 10px 30px rgba(40, 40, 30, 0.18);
  }
  .card-art { position: absolute; inset: 0; }
  .brand {
    position: absolute; left: 0; right: 0; top: 264px;
    text-align: center;
  }
  .brand-name {
    font-family: "Questrial", sans-serif;
    font-size: 46px; letter-spacing: 1px; line-height: 1;
    color: var(--ink-teal);
    text-transform: uppercase;
    white-space: nowrap;
  }
  .brand-tagline {
    margin-top: 8px;
    font-family: "Questrial", sans-serif;
    font-size: 17px; letter-spacing: 1.5px;
    color: var(--ink-dark);
    text-transform: uppercase;
    white-space: nowrap;
  }
  .contact {
    position: absolute; left: 0; right: 0; top: 438px;
    text-align: center;
    font-family: "Mulish", sans-serif;
  }
  .contact-name {
    font-size: 30px; font-weight: 700; letter-spacing: 1.5px;
    color: var(--ink-name);
    white-space: nowrap;
  }
  .contact-line {
    margin-top: 18px;
    font-size: 24px; color: var(--ink-light);
    white-space: nowrap;
  }
  .contact-line .divider { color: var(--slash); margin: 0 12px; }
</style>
</head>
<body>
  <div class="card">
    <svg class="card-art" width="1050" height="600" viewBox="0 0 1050 600">
      <defs>
        <linearGradient id="green-band" x1="0" y1="0" x2="1" y2="0">
          <stop offset="0" stop-color="var(--band-green)"/>
          <stop offset="0.5" stop-color="var(--band-green-dark)"/>
          <stop offset="1" stop-color="var(--band-green)"/>
        </linearGradient>
        <linearGradient id="teal-band" x1="0" y1="0" x2="0" y2="1">
          <stop offset="0" stop-color="var(--band-teal)"/>
          <stop offset="1" stop-color="var(--band-teal-dark)"/>
        </linearGradient>
        <radialGradient id="leaf-haze-light">
          <stop offset="0" stop-color="#dcdad2" stop-opacity="0.7"/>
          <stop offset="1" stop-color="#dcdad2" stop-opacity="0"/>
        </radialGradient>
        <radialGradient id="leaf-haze-dark">
          <stop offset="0" stop-color="#3b7a70" stop-opacity="0.8"/>
          <stop offset="1" stop-color="#3b7a70" stop-opacity="0"/>
        </radialGradient>
      </defs>
      <rect class="band-top" x="0" y="0" width="1050" height="218" fill="url(#green-band)"/>
      <rect class="band-middle" x="0" y="218" width="1050" height="158" fill="var(--band-frost)"/>
      <rect class="band-bottom" x="0" y="376" width="1050" height="224" fill="url(#teal-band)"/>
      <path class="logo-arch" d="M338 218 A 187 167 0 0 1 712 218 Z" fill="var(--band-frost)"/>
      <circle class="brand-mark" cx="525" cy="180" r="58" fill="var(--ink-teal)"/>
      <rect role="img" aria-label="faint leafy branch decoration" x="0" y="218" width="150" height="158" fill="url(#leaf-haze-light)"/>
      <rect role="img" aria-label="faint leafy branch decoration" x="900" y="218" width="150" height="158" fill="url(#leaf-haze-light)"/>
      <rect role="img" aria-label="faint tree and leaf decoration" x="0" y="376" width="220" height="224" fill="url(#leaf-haze-dark)"/>
      <rect role="img" aria-label="faint tree and leaf decoration" x="830" y="376" width="220" height="224" fill="url(#leaf-haze-dark)"/>
    </svg>

    <div class="brand">
      <div class="brand-name">Steadfast Grove</div>
      <div class="brand-tagline">Roots, Community &amp; Stillness</div>
    </div>

    <div class="contact">
      <div class="contact-name">JORDAN ELLERY</div>
      <div class="contact-line">General Manager<span class="divider">/</span>+555-014-2298</div>
    </div>
  </div>
</body>
</html>
```